PillPeak website blog. Simple medical advice given in clear yes or no answers that save people money

I am developing a new web page that provides medical care cost savings at the consumers' fingertips. I need a web page that is clean, concise, and attractive for me to put my valuable medical information on. The information I provide is simple to obtain, yet very valuable to the consumer, and answered in a yes or no format. For example, A person may wonder if they need an antibiotic for cold like symptoms. Seeing a doctor for an antibiotic is very expensive. But with simple and clear advice at their fingertips, they can confidently avoid having to pay $200 or more to see a doctor and get an antibiotic. This is kind of like consumer reports for medical services.

Target Market(s)

People who are savvy shoppers and want to save money on healthcare. Likely younger ages between 21 and 60, who are mobile, readily use iphones, and want strong evidence based research to guide their decisions.

Industry/Entity Type

Coding

Number of Pages Required

Colors

Requirements
Must have
• A template on the "Question" and "Answer" page that can be edited many times that can be edited many times. The Confidence rating scale would need to be edited as well. The "Date Researched" the "PillPeak Pilluminate" and "References" all need to be able to be edited. This website must be very clear and simple to understand. A medical question is posed with a yes or no answer, then answered and given a confidence rating, we then tell them how much money they saved by going to our website.
Nice to have
• We want this to be slightly fun, vibrant, warm and inviting. This will be sometime later converted into an app format. Quirky, some humor to keep it interesting.
Should not have
• No sterile looking medical images. Not boring.

```html
<!DOCTYPE html>
<html lang="en">
<head>
<meta charset="utf-8">
<title>PillPeak — Clear Valuable Health Advice</title>
<link href="https://fonts.googleapis.com/css2?family=PT+Serif:wght@400;700&family=Roboto:wght@400;500&display=swap" rel="stylesheet">
<style>
:root{
  --brand-red:#d9001b;
  --brand-blue:#1560b0;
  --menu-dark:#1462b2;
  --menu-light:#2f86d4;
  --ink:#111111;
  --hero-deep:#030c18;
  --hero-mid:#0a2a52;
  --footer:#121212;
  --white:#ffffff;
}
*{box-sizing:border-box;margin:0;padding:0}
html,body{width:1200px;height:1029px;overflow:hidden;background:var(--white)}
body{font-family:"PT Serif",serif;color:var(--ink);position:relative}

.site-header{position:absolute;left:0;top:0;width:1200px;height:161px;background:var(--white)}
.brand{position:absolute;left:88px;top:56px;display:flex;align-items:center;gap:10px}
.brand-dot{width:26px;height:26px;border-radius:50%;background:var(--brand-red)}
.brand-name{font-family:"PT Serif",serif;font-weight:700;font-size:34px;color:var(--brand-blue)}
.tagline{position:absolute;left:331px;top:67px;font-weight:700;font-size:20px;letter-spacing:.3px;word-spacing:6px;white-space:nowrap}
.search{position:absolute;left:912px;top:56px;width:197px;height:47px;border:1px solid #222;border-radius:24px;box-shadow:0 3px 6px rgba(0,0,0,.15);display:flex;align-items:center;padding:0 16px;font-family:"Roboto",sans-serif;font-size:15px;color:#333;justify-content:space-between}

.main-nav{position:absolute;left:0;top:161px;width:1200px;height:63px;background:var(--brand-red);display:flex;align-items:center;justify-content:center;gap:40px}
.main-nav a{color:var(--white);text-decoration:none;font-size:16.5px;text-transform:uppercase}

.hero{position:absolute;left:0;top:224px;width:1200px;height:568px;background:radial-gradient(ellipse at 75% 55%,var(--hero-mid) 0%,#06192f 45%,var(--hero-deep) 85%)}
.hero-art{position:absolute;right:0;top:40px;width:400px;height:528px;background:radial-gradient(circle at 65% 50%,rgba(60,160,255,.55) 0%,rgba(20,90,180,.3) 45%,rgba(10,40,80,0) 75%)}
.side-menu{position:absolute;left:1px;top:61px;width:295px;list-style:none}
.side-menu li{height:65.4px;display:flex;align-items:center;justify-content:center;color:var(--white);font-size:19.5px;border-bottom:1px solid #0b3e78;background:var(--menu-dark)}
.side-menu li:nth-child(even){background:var(--menu-light)}
.hero-copy{position:absolute;left:344px;top:208px;color:var(--white);font-weight:700;text-transform:uppercase}
.hero-copy .big{font-size:39px;line-height:1}
.hero-copy .mid{font-size:27px;display:block;margin-top:34px;line-height:1}
.hero-copy .row{margin-top:24px;display:flex;align-items:baseline;gap:10px}
.hero-copy .row .big{font-size:39px}
.slider-controls{position:absolute;left:346px;top:389px;display:flex;gap:8px}
.slider-controls span{width:26px;height:26px;border-radius:50%;background:rgba(0,0,0,.45);display:flex;align-items:center;justify-content:center}

.site-footer{position:absolute;left:0;top:792px;width:1200px;height:237px;background:var(--footer);color:var(--white)}
.footer-title{position:absolute;font-size:22px;font-weight:400}
.copyright{position:absolute;left:90px;top:95px;font-family:"Roboto",sans-serif;font-size:15px;color:#e6e6e6}
.social{position:absolute;left:93px;top:134px;display:flex;gap:13px}
.social span{width:30px;height:30px;border:1.5px solid var(--white);border-radius:50%}
.signup{position:absolute;left:742px;top:94px;width:368px;height:45px;display:flex}
.signup .field{flex:1;background:var(--white);color:#333;font-family:"Roboto",sans-serif;font-size:15px;display:flex;align-items:center;padding-left:13px}
.signup .send{width:39px;background:var(--brand-red);display:flex;align-items:center;justify-content:center}
.ask{position:absolute;left:741px;top:153px;font-family:"Roboto",sans-serif;font-size:16px}
</style>
</head>
<body>
<header class="site-header">
  <div class="brand"><span class="brand-dot"></span><span class="brand-name">PillPeak</span></div>
  <p class="tagline">CLEAR VALUABLE HEALTH ADVICE RIGHT NOW</p>
  <div class="search"><span>Search</span>
    <svg width="15" height="15" viewBox="0 0 16 16"><circle cx="6.5" cy="6.5" r="5" fill="none" stroke="#222" stroke-width="2.2"/><line x1="10.3" y1="10.3" x2="14.5" y2="14.5" stroke="#222" stroke-width="2.5" stroke-linecap="round"/></svg>
  </div>
</header>

<nav class="main-nav">
  <a>Prev/Screening</a><a>Women's Health</a><a>Men'Health</a><a>Meds</a><a>Surgery</a><a>Imagery</a><a>Peds</a><a>Contact Us</a>
</nav>

<section class="hero">
  <div class="hero-art" role="img" aria-label="Glowing blue hexagon grid of medical icons"></div>
  <ul class="side-menu">
    <li>Who we are?</li><li>How it works</li><li>How we Know</li><li>Evidence Based Research</li><li>Dr.Whitcombe</li><li>Who we are not</li><li>Are we biased?</li>
  </ul>
  <div class="hero-copy">
    <div class="big">Don't spend another</div>
    <span class="mid">Clinic on your health before</span>
    <div class="row"><span class="mid" style="margin:0">Checking us out !</span><span class="big">It's free</span></div>
  </div>
  <div class="slider-controls">
    <span><svg width="10" height="12" viewBox="0 0 10 12"><path d="M7 1 2 6l5 5" fill="none" stroke="#fff" stroke-width="1.8"/></svg></span>
    <span><svg width="10" height="12" viewBox="0 0 10 12"><path d="M3 1l5 5-5 5" fill="none" stroke="#fff" stroke-width="1.8"/></svg></span>
  </div>
</section>

<footer class="site-footer">
  <h3 class="footer-title" style="left:90px;top:49px">Disclaimer</h3>
  <p class="copyright">© Copyright 2018 . All Rights Reserved.</p>
  <div class="social"><span></span><span></span><span></span><span></span></div>
  <h3 class="footer-title" style="left:741px;top:49px;font-size:25px">Become a pillpeak today!</h3>
  <div class="signup"><div class="field">Enter Email</div>
    <div class="send"><svg width="18" height="18" viewBox="0 0 18 18"><path d="M17 1 1 8l6 2 2 6z" fill="#fff"/></svg></div>
  </div>
  <p class="ask">Ask a Question Here! If it is Worthy,Will post it!</p>
</footer>
</body>
</html>
```